Puffy Clouds Cotton Candy

Looking for a logo design and business cards to help a 13 year old entrepreneur promote her cotton candy business.
Contact Information for Business Card
Name, Phone & Email
Colors
E54698
E96AAD
F1A4CE
F9D9EA
FCEFF6
A7469A
B969AE
D3A5CF
EDDBEB
F8F0F9
6B429C
8869AF
B7A5CE
E3DAEB
F3F0F8
Requirements
Must have
- A fun feel that is appropriate for a teenage girl selling cotton candy

```html
<!DOCTYPE html>
<html lang="en">
<head>
<meta charset="UTF-8">
<title>Puffy Clouds Cotton Candy – Business Card</title>
<link href="https://fonts.googleapis.com/css2?family=Poppins:wght@600&family=Questrial&display=swap" rel="stylesheet">
<style>
  :root {
    --pink: #E54698;
    --pink-light: #E96AAD;
    --magenta: #A7469A;
    --purple: #6B429C;
    --purple-mid: #8869AF;
    --white: #FFFFFF;
    --backdrop: #D6D6D8;
    --card-w: 540px;
    --card-h: 310px;
  }
  * { box-sizing: border-box; margin: 0; padding: 0; }
  html, body {
    width: 1200px; height: 800px; overflow: hidden;
    background: var(--backdrop);
  }
  .sheet {
    width: 1200px; height: 800px;
    display: flex; align-items: center; justify-content: center; gap: 40px;
  }
  .card {
    position: relative;
    width: var(--card-w); height: var(--card-h);
    border-radius: 22px;
    overflow: hidden;
    border: 2px solid var(--pink);
    box-shadow: 0 14px 30px rgba(0,0,0,0.18);
  }

  /* Front */
  .card--front { background: var(--white); }
  .band { position: absolute; }
  .band--pink {
    left: 0; top: 170px; width: 380px; height: 62px;
    background: var(--pink);
  }
  .band--purple {
    right: 0; top: 58px; width: 110px; height: 52px;
    background: var(--purple);
  }
  .brand-disc {
    position: absolute; left: 330px; top: 40px;
    width: 150px; height: 150px; border-radius: 50%;
    background: var(--white);
    border: 5px solid var(--pink);
    display: flex; align-items: center; justify-content: center;
    text-align: center;
  }
  .brand-name {
    font-family: "Poppins", sans-serif; font-weight: 600;
    color: var(--pink); font-size: 17px; line-height: 1.15;
  }
  .identity { position: absolute; left: 34px; top: 96px; }
  .identity__name {
    font-family: "Poppins", sans-serif; font-weight: 600;
    font-size: 24px; color: var(--pink); line-height: 1.1;
  }
  .identity__role {
    font-family: "Questrial", sans-serif;
    font-size: 15px; color: var(--purple);
  }
  .contact {
    position: absolute; left: 34px; top: 178px;
    font-family: "Questrial", sans-serif; font-size: 15px;
    color: var(--white); list-style: none; line-height: 1.4;
  }
  .contact li { display: flex; align-items: center; gap: 8px; }
  .contact svg { width: 14px; height: 14px; }
  .address {
    position: absolute; left: 34px; top: 250px;
    font-family: "Questrial", sans-serif; font-size: 15px;
    color: var(--purple); font-style: normal; line-height: 1.35;
  }

  /* Back */
  .card--back {
    background: radial-gradient(circle at 45% 45%, var(--pink) 0%, var(--magenta) 40%, var(--purple) 80%);
    display: flex; flex-direction: column; align-items: center; justify-content: center;
    gap: 14px;
  }
  .back-disc {
    width: 104px; height: 104px; border-radius: 50%;
    border: 5px solid var(--white);
  }
  .back-name {
    font-family: "Poppins", sans-serif; font-weight: 600;
    color: var(--white); text-align: center; line-height: 1.05;
  }
  .back-name__main { display: block; font-size: 38px; }
  .back-name__sub { display: block; font-size: 24px; }
</style>
</head>
<body>
<main class="sheet">
  <section class="card card--front" aria-label="Business card front">
    <div class="band band--pink"></div>
    <div class="band band--purple"></div>
    <div class="brand-disc">
      <span class="brand-name">Puffy Clouds<br>Cotton Candy</span>
    </div>
    <div class="identity">
      <p class="identity__name">Jordan Ellis</p>
      <p class="identity__role">Managing Director</p>
    </div>
    <ul class="contact">
      <li>
        <svg viewBox="0 0 24 24" aria-hidden="true"><path fill="#FFFFFF" d="M6.6 10.8a15.1 15.1 0 0 0 6.6 6.6l2.2-2.2a1 1 0 0 1 1-.25 11.4 11.4 0 0 0 3.6.57 1 1 0 0 1 1 1V20a1 1 0 0 1-1 1A17 17 0 0 1 3 4a1 1 0 0 1 1-1h3.5a1 1 0 0 1 1 1c0 1.25.2 2.45.57 3.57a1 1 0 0 1-.25 1z"/></svg>
        055-987 654 321
      </li>
      <li>
        <svg viewBox="0 0 24 24" aria-hidden="true"><rect x="2" y="5" width="20" height="14" fill="none" stroke="#FFFFFF" stroke-width="2"/><path d="M2 6l10 7 10-7" fill="none" stroke="#FFFFFF" stroke-width="2"/></svg>
        hello@puffyclouds.com
      </li>
    </ul>
    <address class="address">17, Sugar Street, Riverton<br>30218, Country Name</address>
  </section>

  <section class="card card--back" aria-label="Business card back">
    <div class="back-disc"></div>
    <p class="back-name">
      <span class="back-name__main">Puffy Clouds</span>
      <span class="back-name__sub">Cotton Candy</span>
    </p>
  </section>
</main>
</body>
</html>
```